Health and Fitness Club requires membership pack

We need a membership pack, like this style (http://www.sheetmakersvault.co.uk/images/A4_pocket_folder_round.jpg) a4 sized.

The front of it should contain our logo, the entire thing should be in the style of our brand/concept. On the inside left side there should be space for copy which we will provide once the design has been selected (approximately 500 words).

At the bottom of the left page inside, should be the following:
telephone icon | zqt icon
pixelbrook logo | chirpnet logo | vuo logo | email logo

with the relevant contact details for our company, underneath this should be our website written so that it occupies the entire width of the page.

our website is www. v o r t a g r i p . ae and our logo is attached

i have included a flyer we recently produced to give you an idea of the creative direction of the brand..

```html
<!DOCTYPE html>
<html lang="en">
<head>
<meta charset="utf-8">
<title>Vortagrip Membership Pack</title>
<link rel="stylesheet" href="https://fonts.googleapis.com/css2?family=Arimo:wght@400;700&display=swap">
<style>
  :root {
    --backdrop: #e6e2dc;
    --paper: #ffffff;
    --paper-shade: #d6d7d9;
    --brand-red: #ec1c24;
    --brand-black: #000000;
    --ink: #222222;
  }
  * { box-sizing: border-box; margin: 0; padding: 0; }
  html, body { width: 1200px; height: 1132px; overflow: hidden; }
  body {
    position: relative;
    background: var(--backdrop);
    font-family: "Arimo", Arial, sans-serif;
    color: var(--ink);
  }
  .page {
    position: absolute;
    top: 21px;
    width: 556px;
    height: 770px;
    background: linear-gradient(90deg, var(--paper-shade) 0%, #f1f1f2 30%, var(--paper) 60%);
    box-shadow: 0 3px 8px rgba(0,0,0,.35);
  }
  .page--inside-left { left: 44px; }
  .page--inside-right { left: 600px; }
  .pocket-art { position: absolute; left: 0; top: 0; width: 556px; height: 770px; }

  .brand-mark {
    position: absolute;
    display: flex;
    align-items: center;
    gap: 8px;
    transform: translateX(-50%);
    white-space: nowrap;
  }
  .brand-mark__dot {
    width: 22px; height: 22px; border-radius: 50%;
    background: var(--brand-red);
  }
  .brand-mark__name {
    font-weight: 700;
    color: var(--brand-black);
    letter-spacing: 1px;
  }
  .brand-mark--large { left: 294px; top: 112px; }
  .brand-mark--large .brand-mark__name { font-size: 34px; }
  .brand-mark--large .brand-mark__dot { width: 30px; height: 30px; }
  .brand-mark--small { left: 278px; top: 666px; }
  .brand-mark--small .brand-mark__name { font-size: 20px; }

  .tagline {
    position: absolute;
    left: 20px; right: 20px; top: 271px;
    text-align: center;
    font-size: 13px;
    line-height: 17px;
  }

  .contact {
    position: absolute;
    left: 0; right: 0; top: 715px;
    text-align: center;
  }
  .contact__address { font-size: 16px; margin-bottom: 8px; }
  .contact__lines {
    display: flex; justify-content: center; gap: 16px;
    font-size: 13.5px;
  }
  .contact__item { display: flex; align-items: center; gap: 4px; }
  .contact__item svg { width: 12px; height: 12px; }

  .pocket-flap {
    position: absolute;
    left: 102px; top: 791px;
    width: 497px; height: 274px;
    background: var(--brand-red);
    border-bottom-left-radius: 120px;
    box-shadow: 0 3px 8px rgba(0,0,0,.35);
  }
  .pocket-flap .brand-mark { left: 248px; top: 110px; }
  .pocket-flap .brand-mark__name { font-size: 22px; color: var(--paper); }
  .pocket-flap .brand-mark__dot { background: var(--brand-black); }
</style>
</head>
<body>
  <section class="page page--inside-left">
    <div class="brand-mark brand-mark--small">
      <span class="brand-mark__dot"></span>
      <span class="brand-mark__name">VORTAGRIP</span>
    </div>
    <div class="contact">
      <p class="contact__address">#0000, Street Name, Area Name, city Name Country Code.</p>
      <div class="contact__lines">
        <span class="contact__item">
          <svg viewBox="0 0 12 12" aria-hidden="true"><path d="M3 1l2 2-1 1.5c.6 1.3 1.6 2.3 2.9 2.9L8.4 6.4l2 2-1.4 1.8C5 10 2 7 1.5 3z" fill="#222"/></svg>
          000-XXX-0000
        </span>
        <span class="contact__item">
          <svg viewBox="0 0 12 12" aria-hidden="true"><rect x="3" y="1" width="6" height="10" rx="1" fill="none" stroke="#222" stroke-width="1.4"/></svg>
          000-XXX-0000
        </span>
        <span class="contact__item">
          <svg viewBox="0 0 12 12" aria-hidden="true"><rect x="3" y="1" width="6" height="4" fill="#222"/><rect x="1" y="5" width="10" height="6" rx="1" fill="#222"/></svg>
          000-XXX-0000
        </span>
        <span class="contact__item">
          <svg viewBox="0 0 12 12" aria-hidden="true"><rect x="1" y="3" width="10" height="7" fill="none" stroke="#222" stroke-width="1.2"/><path d="M1 3l5 4 5-4" fill="none" stroke="#222" stroke-width="1.2"/></svg>
          yourname@mail.com
        </span>
      </div>
    </div>
  </section>

  <section class="page page--inside-right">
    <div class="brand-mark brand-mark--large">
      <span class="brand-mark__dot"></span>
      <span class="brand-mark__name">VORTAGRIP</span>
    </div>
    <p class="tagline">Your Vortagrip Training Home, your space to get fit and stay in shape! A place where<br>everyone knows your name, no prison turnstiles here!</p>
    <svg class="pocket-art" viewBox="0 0 556 770" aria-hidden="true">
      <polygon points="3,770 331,584 331,770" fill="var(--brand-red)"/>
      <polygon points="331,584 556,457 556,770 331,770" fill="var(--brand-black)"/>
      <line x1="3" y1="768" x2="556" y2="455" stroke="#ffffff" stroke-width="3"/>
      <line x1="3" y1="764" x2="556" y2="451" stroke="#555" stroke-width="1"/>
    </svg>
  </section>

  <section class="pocket-flap">
    <div class="brand-mark">
      <span class="brand-mark__dot"></span>
      <span class="brand-mark__name">VORTAGRIP</span>
    </div>
  </section>
</body>
</html>
```